Residential Mortgage Leader needs Wordpress Design

Looking for a home page website design for a client. We develop using the WordPress platform and would prefer the design be at least loosely based on an existing WordPress template. Attached files have many notes from our creative brief with client. The site must be responsive. Approved, basic wireframe attached. There is room for interpretation.

Existing web site: http://www.marisolkettering.example/

The Marisol Kettering Team relies on strong systems to deliver an on-time, done-right, friendly experience. Marisol offers mortgages and refinancing services throughout the United States. She is a successful Brookvale Funding agent who strives to be an active part of her community. She would like to focus the site on her team, rather than just her.

Difference makers...
When you work with the Marisol Kettering team you get a high level of expertise and a friendly experience.

She has amazing credentials. Marisol is widely recognized as a top producer for her company, and has earned a number of awards and honors for her customer service.

Marisol's team is very engaged and enjoys sharing social comments or photos from their community.

Imagery:
* Friendly, warm imagery, preferably of her team or an image to represent her team
* Clean and crisp
* Professional / Experts in mortgage and refinance
* Clean / Good use of white space
Updates

When possible, please use imagery from the DFW area. The client mentioned they would prefer not to see stock images. Thanks.

Amend that- creative use of stock images, however, is fine. A few designs have used stock imagery, but in a well-considered manner.

We added some photos and graphics that are local. We are Dallas / Ft. Worth, Plano, Frisco, Texas. We also added some examples of photos to use for the "In the Community" area. Stock photos of business folks just doesn't fit there. Thanks!

Target Market(s)

They service a lot of builders, but also work with homeowners. Their typical client is usually a woman searching for mortgage services online. She typically has a family and may refer her husband to Marisol's team. Keep in mind, however, they also see a number of other scenarios. Most of their clients are middle to high-end borrowers.

Industry/Entity Type

It Company

Requirements
Must have
• Design should be developed using program such as Photoshop or Fireworks or Illustrator as last preference. Ideally, the design would be based on an existing responsive WordPress theme, which we would customize. You must include the name of the target theme. The footer should include lots of space for disclaimers and legal language. Site navigation should include these choices: "Home, About, Builders, Mortgage Info, Approval, Blog, Contact"
Nice to have
• Blog, social media and photos area. Use of the already approved style prototype with colors and fonts (Lato- a Google font, Times New Roman and Cookie-a decorative Google font). However, we are open to interpretation.
Should not have
• Hard to read fonts or a lack of white space.

```html
<!DOCTYPE html>
<html lang="en">
<head>
<meta charset="utf-8">
<title>Brookvale Funding – Marisol Kettering Team</title>
<link href="https://fonts.googleapis.com/css2?family=Montserrat:wght@400;500;600;700&display=swap" rel="stylesheet">
<style>
:root{
  --red:#c0311d;
  --red-bright:#d83a22;
  --ink:#3a3a3a;
  --muted:#9a9a9a;
  --paper:#ffffff;
  --band:#f0f0f0;
  --footer:#2c2c2c;
  --footer-deep:#262626;
  --nav-top:#6a6a6a;
  --nav-bottom:#3e3e3e;
}
*{margin:0;padding:0;box-sizing:border-box}
html,body{width:834px;height:1200px;overflow:hidden}
body{font-family:"Montserrat",Arial,sans-serif;color:var(--ink);background:var(--paper);position:relative}
.abs{position:absolute}
ul{list-style:none}

/* header */
.site-header{position:absolute;left:0;top:0;width:834px;height:101px;background:var(--paper)}
.brand-name{left:90px;top:34px;font-size:25px;font-weight:700;color:var(--red);letter-spacing:-0.5px}
.brand-sub{left:91px;top:63px;font-size:11px;font-weight:600;color:#555}
.work-label{right:90px;top:38px;font-size:9px;color:#555;letter-spacing:.5px}
.work-phone{right:90px;top:50px;font-size:18px;color:var(--red)}
.work-mail{right:90px;top:75px;font-size:9px;color:#333}

/* nav */
.main-nav{position:absolute;left:0;top:101px;width:834px;height:41px;background:linear-gradient(var(--nav-top),var(--nav-bottom))}
.main-nav ul{display:flex;position:absolute;left:117px;top:14px;font-size:9.5px;color:#fff}
.main-nav li::after{content:"|";margin:0 12px}
.main-nav li:last-child::after{content:""}

/* hero */
.hero{position:absolute;left:0;top:142px;width:834px;height:280px;background:linear-gradient(160deg,#bdbdbd,#7d7d7d 45%,#a8a8a8 70%,#5e5e5e)}
.hero-photo{left:132px;top:69px;width:278px;height:152px;border:5px solid #e9e9e9;background:linear-gradient(90deg,#eef0f2,#cfd5dc 45%,#8a8f98 70%,#e8ebee)}
.hero-copy{left:410px;top:69px;width:302px;height:94px;background:rgba(40,40,40,.85);padding:10px 10px 0 20px}
.hero-copy h2{font-size:15.5px;font-weight:500;color:var(--red-bright);margin-bottom:6px}
.hero-copy p{font-size:7.6px;line-height:15.2px;color:#fff}
.btn{top:183px;height:32px;font-size:12px;font-weight:500;color:#fff;display:flex;align-items:center;justify-content:center}
.btn-start{left:424px;width:139px;background:#4a4a4a}
.btn-know{left:572px;width:140px;background:var(--red)}
.hero-arrow{top:134px;width:31px;height:31px;border-radius:50%;background:#fff}

/* credentials */
.credentials{position:absolute;left:0;top:422px;width:834px;height:261px;background:var(--red)}
.cred-panel{left:299px;top:0;width:452px;height:261px;background:var(--paper);box-shadow:0 0 6px rgba(0,0,0,.3)}
.cred-notch{left:299px;top:116px;width:0;height:0;border-top:16px solid transparent;border-bottom:16px solid transparent;border-left:11px solid var(--red)}
.cred-col h3{font-size:12.5px;font-weight:500;margin-bottom:7px}
.cred-col .lead{font-size:9px}
.cred-col .body{font-size:7.6px;line-height:16.8px;text-align:justify}
.cred-main{left:104px;top:20px;width:180px;color:#fff}
.cred-main h3{color:#fff}
.cred-main .body{position:absolute;top:125px;left:3px;width:180px}
.cred-side{top:20px;width:200px}
.cred-side h3{color:var(--red)}
.cred-side .body{position:absolute;top:117px;left:4px;width:200px;color:var(--muted)}
.cred-icon{position:absolute}

/* community */
.community{position:absolute;left:0;top:683px;width:834px;height:295px;background:var(--band)}
.community-title{position:absolute;top:12px;width:834px;text-align:center;font-size:16.5px;font-weight:500;color:var(--red)}
.community-sub{position:absolute;top:38px;width:834px;text-align:center;font-size:11.5px;color:#444}
.community-rule{left:0;top:55px;width:834px;height:1px;background:#dcdcdc}
.col-title{font-size:12.5px;font-weight:500;color:var(--red)}
.blog-list{left:91px;top:107px;font-size:9.3px;color:#333}
.blog-list li{height:24.2px;display:flex;align-items:flex-start}
.blog-list li::before{content:"";width:9px;height:9px;border-radius:50%;background:#2a2a2a;margin:1px 11px 0 0;flex:none}
.social-item{left:312px;width:210px;height:48px}
.social-thumb{position:absolute;left:0;top:0;width:56px;height:48px;border:1px solid #ddd}
.social-text{position:absolute;left:65px;top:2px;width:145px;font-size:7.5px;line-height:14.6px;color:#555}
.social-text span{color:var(--red)}
.community-box{left:535px;top:67px;width:208px;height:197px;background:var(--paper);box-shadow:0 0 5px rgba(0,0,0,.18);padding:10px 10px}
.community-box h4{font-size:12px;font-weight:500;color:#333}
.person{position:absolute;width:70px;text-align:center;font-size:7.8px;color:#888}
.person .shot{width:70px;height:56px;margin-bottom:3px}

/* footer */
.site-footer{position:absolute;left:0;top:978px;width:834px;height:222px;background:var(--footer)}
.footer-bottom{left:0;top:165px;width:834px;height:57px;background:var(--footer-deep)}
.foot-title{font-size:12.5px;font-weight:400;color:var(--red-bright)}
.foot-text{font-size:8.6px;color:#fff;line-height:23px}
.agent-photo{left:90px;top:28px;width:97px;height:76px;background:linear-gradient(135deg,#6b4a36,#b88a6c 55%,#4a3a30)}
.agent-name{left:90px;top:111px;font-size:9.5px;color:var(--red-bright)}
.agent-meta{left:90px;top:127px;font-size:8.3px;color:#fff;line-height:16px}
.flag{top:50px;width:22px;height:16px}
.housing-badge{left:537px;top:60px;width:24px;height:22px;border:2px solid #fff;border-radius:2px}
.connect-row{left:632px;width:98px;height:19px;display:flex;align-items:center;justify-content:space-between;font-size:8.6px;color:#fff}
.connect-row .dot{width:19px;height:19px;border-radius:50%;border:2px solid #fff;background:var(--footer)}
.copyright{left:0;top:192px;width:834px;text-align:center;font-size:8.5px;color:#fff;padding-right:50px}
</style>
</head>
<body>

<header class="site-header">
  <div class="abs brand-name">Brookvale Funding</div>
  <div class="abs brand-sub">A Ridgeway Capital Company</div>
  <div class="abs work-label">WORK WTH US</div>
  <div class="abs work-phone">555-014-2290</div>
  <div class="abs work-mail">E-Mail :info@brookvalefunding.example</div>
</header>

<nav class="main-nav">
  <ul>
    <li>Home</li><li>About</li><li>Builders</li><li>Mortgage Info</li><li>Approval</li><li>Blog</li><li>Contact</li>
  </ul>
</nav>

<section class="hero" role="img" aria-label="Black and white aerial view of downtown skyscrapers">
  <div class="abs hero-photo" role="img" aria-label="Loan officer presenting at a whiteboard to a small team"></div>
  <div class="abs hero-copy">
    <h2>Earn Your Business</h2>
    <p>Marisol Kettering is a Senior Loan Officer and Branch Manager with Brookvale Funding, A Ridgeway Capital Company. With over 8 years experience, Marisol has earned several notable awards. She has been a Brookvale Power Producer for the last 7 years.</p>
  </div>
  <div class="abs btn btn-start">Start Here</div>
  <div class="abs btn btn-know">Get To know Us</div>
  <div class="abs hero-arrow" style="left:53px">
    <svg width="31" height="31" viewBox="0 0 31 31"><path d="M18 9l-6 6.5 6 6.5" fill="none" stroke="#333" stroke-width="2.5"/></svg>
  </div>
  <div class="abs hero-arrow" style="left:751px">
    <svg width="31" height="31" viewBox="0 0 31 31"><path d="M13 9l6 6.5-6 6.5" fill="none" stroke="#333" stroke-width="2.5"/></svg>
  </div>
</section>

<section class="credentials">
  <div class="abs cred-panel"></div>
  <div class="abs cred-notch"></div>

  <div class="abs cred-col cred-main">
    <h3>Our Credentials</h3>
    <p class="lead">A top producer ,top Notch</p>
    <svg class="cred-icon" style="left:66px;top:52px" width="43" height="57" viewBox="0 0 43 57">
      <path d="M2 2h30l9 9v44H2z" fill="#fff"/>
      <g stroke="var(--red)" stroke-width="2.2">
        <path d="M9 16h4M16 16h18M9 23h4M16 23h18M9 30h4M16 30h18M9 37h4M16 37h18M9 44h4M16 44h18"/>
      </g>
    </svg>
    <p class="body">Lorem Ipsum is simply dummy text of the printing and typesetting industry. Lorem Ipsum has been the industry's standard dummy</p>
  </div>

  <div class="abs cred-col cred-side" style="left:312px">
    <h3>Awards</h3>
    <p class="lead">Lorem Ipsum is simply dummy</p>
    <svg class="cred-icon" style="left:88px;top:54px" width="34" height="42" viewBox="0 0 34 42">
      <path d="M9 24L3 38l7-2 3 6 5-13zM25 24l6 14-7-2-3 6-5-13z" fill="#444"/>
      <circle cx="17" cy="16" r="14" fill="#444"/>
      <text x="17" y="21" text-anchor="middle" font-size="14" font-weight="700" fill="#fff" font-family="Montserrat,sans-serif">1</text>
    </svg>
    <p class="body">Lorem Ipsum is simply dummy text of the printing and typesetting industry. Lorem Ipsum has been the industry's standard dummy text ever since the 1500s, when an unknown printer took a galley of type and scrambled</p>
  </div>

  <div class="abs cred-col cred-side" style="left:535px">
    <h3>Recognition</h3>
    <p class="lead">A top producer ,top Notch</p>
    <svg class="cred-icon" style="left:89px;top:58px" width="30" height="32" viewBox="0 0 30 32">
      <path d="M15 1l13 6v11c0 7-6 12-13 13C8 30 2 25 2 18V7z" fill="#444"/>
      <circle cx="15" cy="16" r="8" fill="#fff"/>
      <path d="M15 10l1.8 4 4.2.4-3.2 2.8 1 4.2-3.8-2.2-3.8 2.2 1-4.2-3.2-2.8 4.2-.4z" fill="#444"/>
    </svg>
    <p class="body">Lorem Ipsum is simply dummy text of the printing and typesetting industry. Lorem Ipsum has been the industry's standard dummy text ever since the 1500s, when an unknown printer took a galley of type and scrambled</p>
  </div>
</section>

<section class="community">
  <h2 class="community-title">Engaged In Our Community</h2>
  <p class="community-sub">Connect With Us</p>
  <div class="abs community-rule"></div>

  <h3 class="abs col-title" style="left:89px;top:77px">Blog</h3>
  <ul class="abs blog-list">
    <li>Vero eos et accusamus</li>
    <li>Et iusto odio dignissimos</li>
    <li>Ducimus qui blanditiis</li>
    <li>Praesentium voluptatum</li>
    <li>Deleniti atque corrupti quos</li>
    <li>Dolores et quas molestias</li>
    <li>Excepturi sint occaecati</li>
  </ul>

  <h3 class="abs col-title" style="left:312px;top:77px">Social</h3>
  <div class="abs social-item" style="top:108px">
    <div class="social-thumb" role="img" aria-label="Portrait of a team member" style="background:linear-gradient(135deg,#e8e8e8,#8a6e5c 55%,#3a3a3a)"></div>
    <p class="social-text">Lorem ipsum dolor sit amet, consectetur adipiscing elit, sed do eiusmod tempor <span>...Read More</span></p>
  </div>
  <div class="abs social-item" style="top:163px">
    <div class="social-thumb" role="img" aria-label="Portrait of a team member in a suit" style="background:linear-gradient(135deg,#6a7480,#a98a76 50%,#2a2f3a)"></div>
    <p class="social-text">Lorem ipsum dolor sit amet, consectetur adipiscing elit, sed do eiusmod tempor <span>...Read More</span></p>
  </div>
  <div class="abs social-item" style="top:219px">
    <div class="social-thumb" role="img" aria-label="Portrait of a smiling team member" style="background:linear-gradient(135deg,#3a2a22,#b08468 55%,#5a4030)"></div>
    <p class="social-text">Lorem ipsum dolor sit amet, consectetur adipiscing elit, sed do eiusmod tempor <span>...Read More</span></p>
  </div>

  <div class="abs community-box">
    <h4>In the community</h4>
    <div class="person" style="left:20px;top:32px"><div class="shot" role="img" aria-label="Community member portrait" style="background:linear-gradient(135deg,#d9dde2,#a58470 60%,#f0f0f0)"></div>Tobias Wren</div>
    <div class="person" style="left:121px;top:32px"><div class="shot" role="img" aria-label="Community member portrait" style="background:linear-gradient(135deg,#1f1f1f,#9a7560 55%,#2a2a2a)"></div>Tobias Wren</div>
    <div class="person" style="left:20px;top:113px"><div class="shot" role="img" aria-label="Community member portrait" style="background:linear-gradient(135deg,#6d747c,#b58e76 55%,#4a5058)"></div>Tobias Wren</div>
    <div class="person" style="left:121px;top:113px"><div class="shot" role="img" aria-label="Community member portrait" style="background:linear-gradient(135deg,#f4f4f4,#d09a78 45%,#d8432a)"></div>Tobias Wren</div>
  </div>
</section>

<footer class="site-footer">
  <div class="abs agent-photo" role="img" aria-label="Portrait of Marisol Kettering"></div>
  <div class="abs agent-name">Marisol Kettering</div>
  <div class="abs agent-meta">Branch Manager<br>NMLS #: 40517</div>

  <h4 class="abs foot-title" style="left:222px;top:25px">Address</h4>
  <p class="abs foot-text" style="left:222px;top:49px">Brookvale Funding<br>418 Alder Row Two<br>Cedar Falls, TN(Tennessee)<br>37000-0418 (555) 014- 229-018</p>

  <h4 class="abs foot-title" style="left:353px;top:25px">Misc Languages</h4>
  <div class="abs flag" style="left:353px;background:#2b3f8a" role="img" aria-label="English language"></div>
  <div class="abs flag" style="left:381px;background:linear-gradient(90deg,#2e7a2e 40%,#c8281e 40%)" role="img" aria-label="Portuguese language"></div>
  <div class="abs flag" style="left:409px;background:linear-gradient(#f4f4f4 50%,#d32030 50%)" role="img" aria-label="Polish language"></div>
  <div class="abs flag" style="left:437px;background:repeating-linear-gradient(#c8281e 0 2.3px,#fff 2.3px 4.6px)" role="img" aria-label="American English language"></div>

  <h4 class="abs foot-title" style="left:500px;top:25px">Equal Housing</h4>
  <div class="abs housing-badge" role="img" aria-label="Equal housing badge"></div>

  <h4 class="abs foot-title" style="left:632px;top:25px">Connect With Us</h4>
  <div class="abs connect-row" style="top:62px"><span class="dot"></span>Chirpline</div>
  <div class="abs connect-row" style="top:88px"><span class="dot"></span>Friendbook</div>
  <div class="abs connect-row" style="top:114px"><span class="dot"></span>Worklink</div>

  <div class="abs footer-bottom"></div>
  <p class="abs copyright">Copyright ©2013 Company Name &nbsp; - All rights reserved</p>
</footer>

</body>
</html>
```